Natural Medicine & Health/Fitness Coaching studio requires web page

Require a innovative web page for a studio that coaches clients to better health, nutrition and fitness. The studio compromises of Clinical Nutritionists, Naturopaths, Rehab Trainers, Personal Trainers and Sport Coaches. Would like to see earthy but bold designs emphasizing nutritional health and athletic performance.
Updates

Design only launched today.

Target Market(s)

All genders from 20's to 60's, as well as families

Industry/Entity Type

Nutritionist

Coding

Coded - Design and coding required

Number of Pages Required

3 page

Colors
abd037
3277b5
fbee3d
fece3e
33b8a4
f04a50

Requirements
Must have
• Online booking system, ability to message
• Home page
• Coaching/Fitness page
• Nutritional Medicine page
• Must be suitable for both Fitness and Nutrition

```html
<!DOCTYPE html>
<html lang="en">
<head>
<meta charset="utf-8">
<title>Verdant Form Nutritional Therapy</title>
<link href="https://fonts.googleapis.com/css2?family=Cinzel:wght@400&family=Open+Sans:ital,wght@0,400;0,600;0,700;1,700&display=swap" rel="stylesheet">
<style>
:root{
  --green:#8dc63f;
  --green-dark:#5e9e2a;
  --blue:#1b75bb;
  --yellow:#fbbf2e;
  --ink:#222;
  --text:#555;
  --muted:#777;
  --panel:#f3f3f3;
  --badge:#c9c9c9;
  --white:#fff;
}
*{box-sizing:border-box;margin:0;padding:0}
html,body{width:1200px;height:4167px;overflow:hidden;background:var(--white)}
body{font-family:"Open Sans",Arial,sans-serif;color:var(--text);position:relative}
.serif{font-family:"Cinzel",Georgia,serif;font-weight:400;color:var(--ink)}
section,header,footer{position:absolute;left:0;width:1200px}

/* header */
.site-header{top:0;height:118px}
.brand{position:absolute;left:110px;top:16px;display:flex;align-items:center;gap:12px;color:var(--green-dark);font-weight:700}
.brand-dot{width:22px;height:22px;border-radius:50%;background:var(--green)}
.brand-name{font-size:40px;line-height:44px}
.brand-sub{font-size:15px;line-height:18px;letter-spacing:1px}
.call{position:absolute;right:110px;top:22px;font-size:16px;color:var(--ink);display:flex;align-items:center;gap:8px}
.call b{font-weight:600;color:var(--muted)}
.main-nav{position:absolute;right:110px;top:74px;display:flex;gap:26px;font-size:15px;color:var(--ink);align-items:center;text-transform:uppercase}
.main-nav .active{color:var(--green)}

/* hero */
.hero{top:118px;height:568px;background:linear-gradient(100deg,#4f6a35 0%,#6f8a45 40%,#8aa35a 60%,#a4bd72 100%)}
.hero-title{position:absolute;left:110px;top:100px;font-size:68px;line-height:84px;color:var(--white);font-family:"Cinzel",Georgia,serif;font-weight:400}
.hero-sub{position:absolute;left:110px;top:292px;font-size:30px;font-weight:700;font-style:italic;color:var(--white)}
.btn-outline{position:absolute;left:110px;top:380px;width:196px;height:62px;border:2px solid var(--white);border-radius:31px;color:var(--white);font-weight:700;font-size:17px;display:flex;align-items:center;justify-content:center}
.hero-dots{position:absolute;left:562px;top:482px;display:flex;gap:6px}
.hero-dots i{width:14px;height:14px;border-radius:50%;border:2px solid var(--white)}
.hero-dots i:first-child{background:var(--white)}

/* welcome */
.welcome{top:686px;height:780px;text-align:center}
.section-title{font-size:33px;letter-spacing:1px}
.welcome .section-title{margin-top:100px}
.lede{width:810px;margin:24px auto 0;font-size:13.5px;line-height:28px;color:var(--muted)}
.services{position:absolute;top:306px;left:0;width:1200px}
.service{position:absolute;width:300px;text-align:center}
.service .ring{width:204px;height:204px;border-radius:50%;margin:0 auto;border:7px solid var(--white);box-shadow:0 0 0 5px currentColor;display:flex;align-items:center;justify-content:center}
.service h3{margin-top:42px;font-size:26px}
.service p{width:270px;margin:14px auto 0;font-size:13.5px;line-height:26px;color:var(--muted)}

/* digestion */
.digestion{top:1465px;height:625px}
.digestion-panel{position:absolute;left:0;top:0;width:600px;height:625px;background:var(--panel)}
.digestion-panel h2{position:absolute;left:110px;top:60px;font-size:36px;line-height:54px}
.tick-list{position:absolute;left:110px;top:200px;width:440px;list-style:none}
.tick-list li{position:relative;padding-left:28px;font-size:15px;line-height:22px;margin-bottom:23px;color:var(--text)}
.tick-list li svg{position:absolute;left:0;top:3px}
.digestion-photo{position:absolute;left:600px;top:0;width:600px;height:625px;background:linear-gradient(135deg,#3a2a24 0%,#7a4a3c 35%,#c08b7a 60%,#e9d8c8 100%)}

/* small stuff */
.calm{top:2090px;height:860px;text-align:center}
.calm .section-title{margin-top:100px}
.tile{position:absolute;color:var(--white);font-size:16px;font-weight:600}
.tile span{position:absolute;left:18px;bottom:22px;right:18px;text-align:left}
.tile.center span{text-align:center;bottom:50px;line-height:28px}

/* partners */
.partners{top:2950px;height:415px;background:var(--panel);text-align:center}
.partners .section-title{margin-top:90px}
.badge{position:absolute;top:196px;background:var(--badge);border-radius:6px}

/* booking */
.booking{top:3365px;height:480px;background:linear-gradient(160deg,#3a72b4,#2b5f9f 60%,#336cad)}
.booking h2{text-align:center;color:var(--white);font-size:36px;margin-top:68px}
.field{position:absolute;background:var(--white);font-size:14px;color:var(--muted);padding:12px 14px}
.btn-submit{position:absolute;left:537px;top:360px;width:126px;height:50px;border-radius:25px;background:var(--green);color:var(--white);font-weight:700;font-size:15px;display:flex;align-items:center;justify-content:center}

/* footer */
.site-footer{top:3845px;height:322px;text-align:center;font-size:14px;color:var(--muted)}
.social{position:absolute;left:0;width:1200px;top:94px;display:flex;justify-content:center;gap:12px}
.social i{width:50px;height:50px;border-radius:50%;border:2px solid var(--green)}
.contact-line{position:absolute;top:178px;width:1200px;display:flex;justify-content:center;gap:14px;align-items:center}
.links{position:absolute;top:218px;width:1200px}
.copy{position:absolute;top:254px;width:1200px}
</style>
</head>
<body>

<header class="site-header">
  <div class="brand">
    <span class="brand-dot"></span>
    <div><div class="brand-name">Verdant Form</div><div class="brand-sub">Nutritional Therapy</div></div>
  </div>
  <div class="call">
    <svg width="16" height="16" viewBox="0 0 24 24"><path fill="#8dc63f" d="M6.6 10.8a15 15 0 0 0 6.6 6.6l2.2-2.2a1 1 0 0 1 1-.25 11.4 11.4 0 0 0 3.6.6 1 1 0 0 1 1 1V20a1 1 0 0 1-1 1A17 17 0 0 1 3 4a1 1 0 0 1 1-1h3.5a1 1 0 0 1 1 1c0 1.25.2 2.45.6 3.6a1 1 0 0 1-.25 1z"/></svg>
    CALL NOW: <b>1 800 555 0134</b>
  </div>
  <nav class="main-nav">
    <span class="active">Home</span><span>About us</span><span>Coaching</span><span>Fitness</span><span>Nutrition</span><span>Contact us</span>
    <svg width="16" height="16" viewBox="0 0 24 24"><circle cx="10" cy="10" r="6.5" fill="none" stroke="#222" stroke-width="3"/><path d="M15 15l6 6" stroke="#222" stroke-width="3"/></svg>
  </nav>
</header>

<section class="hero" role="img" aria-label="Photo of a couple running together on a grassy path">
  <h1 class="hero-title">NUTRITIONAL<br>THERAPY</h1>
  <p class="hero-sub">Healthy liver&amp; gallbladder function</p>
  <span class="btn-outline">BOOK NOW</span>
  <div class="hero-dots"><i></i><i></i><i></i><i></i></div>
</section>

<section class="welcome">
  <h2 class="section-title serif">WELCOME TO VERDANT FORM NUTRITIONAL THERAPY</h2>
  <p class="lede">We all know that healthy eating is important. The Mediterranean style of eating is possibly the most healthful dietary principle and is sometimes also called an "anti-inflammatory" diet. However, if we want to go a little further and make this more specific for healthy liver and gallbladder function, we would include the following:</p>
  <div class="services">
    <div class="service" style="left:97px;color:var(--blue)">
      <div class="ring" style="background:var(--blue)">
        <svg width="90" height="80" viewBox="0 0 24 22"><path fill="#fff" d="M12 21.5l-1.5-1.4C5.4 15.4 2 12.3 2 8.5 2 5.4 4.4 3 7.5 3c1.7 0 3.4.8 4.5 2.1C13.1 3.8 14.8 3 16.5 3 19.6 3 22 5.4 22 8.5c0 3.8-3.4 6.9-8.5 11.5z"/></svg>
      </div>
      <h3 class="serif">NUTRITION</h3>
      <p>Nam libero tempore, cum soluta nobis gendi optio cumque nihil impediquous id quod maxpoime placeaace</p>
    </div>
    <div class="service" style="left:450px;color:var(--yellow)">
      <div class="ring" style="background:var(--yellow)">
        <svg width="110" height="60" viewBox="0 0 110 60"><g fill="#fff"><rect x="6" y="18" width="8" height="24" rx="2"/><rect x="18" y="8" width="12" height="44" rx="3"/><rect x="30" y="26" width="50" height="8"/><rect x="80" y="8" width="12" height="44" rx="3"/><rect x="96" y="18" width="8" height="24" rx="2"/></g></svg>
      </div>
      <h3 class="serif">FITNESS</h3>
      <p>Nam libero tempore, cum soluta nobis gendi optio cumque nihil impediquous id quod maxpoime placeaace</p>
    </div>
    <div class="service" style="left:803px;color:var(--green)">
      <div class="ring" style="background:var(--green)">
        <svg width="96" height="84" viewBox="0 0 96 84"><rect x="6" y="6" width="84" height="56" rx="5" fill="none" stroke="#fff" stroke-width="8"/><rect x="40" y="62" width="16" height="12" fill="#fff"/><rect x="26" y="72" width="44" height="7" rx="2" fill="#fff"/></svg>
      </div>
      <h3 class="serif">ONLINE SERVICES</h3>
      <p>Nam libero tempore, cum soluta nobis gendi optio cumque nihil impediquous id quod maxpoime placeaace</p>
    </div>
  </div>
</section>

<section class="digestion">
  <div class="digestion-panel">
    <h2 class="serif">EAT RIGHT FOR<br>HEALTHY DIGESTION</h2>
    <ul class="tick-list">
      <li><svg width="16" height="16" viewBox="0 0 16 16"><circle cx="8" cy="8" r="8" fill="#1b75bb"/><path d="M4.5 8.2l2.3 2.3 4.7-4.8" fill="none" stroke="#fff" stroke-width="2"/></svg>Bitter foods in meals</li>
      <li><svg width="16" height="16" viewBox="0 0 16 16"><circle cx="8" cy="8" r="8" fill="#1b75bb"/><path d="M4.5 8.2l2.3 2.3 4.7-4.8" fill="none" stroke="#fff" stroke-width="2"/></svg>Ensure meals contain a balance of fats, carbohydrates and proteins</li>
      <li><svg width="16" height="16" viewBox="0 0 16 16"><circle cx="8" cy="8" r="8" fill="#1b75bb"/><path d="M4.5 8.2l2.3 2.3 4.7-4.8" fill="none" stroke="#fff" stroke-width="2"/></svg>Eat fermented foods</li>
      <li><svg width="16" height="16" viewBox="0 0 16 16"><circle cx="8" cy="8" r="8" fill="#1b75bb"/><path d="M4.5 8.2l2.3 2.3 4.7-4.8" fill="none" stroke="#fff" stroke-width="2"/></svg>Don't skip on the fibre</li>
      <li><svg width="16" height="16" viewBox="0 0 16 16"><circle cx="8" cy="8" r="8" fill="#1b75bb"/><path d="M4.5 8.2l2.3 2.3 4.7-4.8" fill="none" stroke="#fff" stroke-width="2"/></svg>Ensure that meal portions are not too big</li>
      <li><svg width="16" height="16" viewBox="0 0 16 16"><circle cx="8" cy="8" r="8" fill="#1b75bb"/><path d="M4.5 8.2l2.3 2.3 4.7-4.8" fill="none" stroke="#fff" stroke-width="2"/></svg>Try not to snack in between meals and have a break from eating</li>
      <li><svg width="16" height="16" viewBox="0 0 16 16"><circle cx="8" cy="8" r="8" fill="#1b75bb"/><path d="M4.5 8.2l2.3 2.3 4.7-4.8" fill="none" stroke="#fff" stroke-width="2"/></svg>Make sure you sit and eat your meals in a peaceful environment</li>
    </ul>
  </div>
  <div class="digestion-photo" role="img" aria-label="Photo of a bowl of yoghurt with berries and granola being eaten with a spoon"></div>
</section>

<section class="calm">
  <h2 class="section-title serif">DON'T SWEAT THE SMALL STUFF</h2>
  <p class="lede">Learning techniques or changing thought patterns to help you rethink what is important and what isn't, is a powerful step for you to improve digestion and detoxification. Getting stressed about every little thing will dysregulate your autonomic nervous system and create long term problems with digestion and detoxification.</p>
  <div class="tile" style="left:111px;top:344px;width:282px;height:180px;background:linear-gradient(160deg,#d9d4cf,#8d8480 70%,#4d4543)" role="img" aria-label="Photo of a person sleeping peacefully"><span>DON'T SKIP ON sleep</span></div>
  <div class="tile" style="left:111px;top:546px;width:282px;height:180px;background:linear-gradient(150deg,#3a6c9a,#8fb5cf 55%,#d98a4a)" role="img" aria-label="Image of a hand touching a DNA strand"><span>FEED YOUR Biochemistry</span></div>
  <div class="tile center" style="left:412px;top:344px;width:376px;height:382px;background:linear-gradient(180deg,#8ca6c2 0%,#b4b0a6 35%,#9c7a3e 65%,#6a5a2c 100%)" role="img" aria-label="Photo of a mountain biker riding a trail through autumn hills"><span>MAKE TIME FOR DOING<br>THINGS you love</span></div>
  <div class="tile" style="left:810px;top:344px;width:282px;height:180px;background:linear-gradient(180deg,#4c86c0,#9cc0dc 55%,#5b6a55)" role="img" aria-label="Photo of a person with raised arms on a mountain top"><span>CLEAN UP YOUR environment</span></div>
  <div class="tile" style="left:810px;top:546px;width:282px;height:180px;background:linear-gradient(180deg,#6f9fc4,#c9d6df 55%,#8a8a88)" role="img" aria-label="Photo of a person in a yoga pose by the sea"><span>CONSIDER YOUR medications</span></div>
</section>

<section class="partners">
  <h2 class="section-title serif">OUR PARTNERS</h2>
  <div class="badge" style="left:315px;width:250px;height:114px" role="img" aria-label="Partner membership badge"></div>
  <div class="badge" style="left:612px;width:270px;height:114px" role="img" aria-label="Partner trainer badge"></div>
</section>

<section class="booking">
  <h2 class="serif" style="color:var(--white)">ONLINE BOOKING</h2>
  <div class="field" style="left:260px;top:145px;width:330px;height:42px">First Name</div>
  <div class="field" style="left:606px;top:145px;width:334px;height:42px">Last Name</div>
  <div class="field" style="left:260px;top:204px;width:330px;height:42px">Email Address</div>
  <div class="field" style="left:606px;top:204px;width:334px;height:42px">Phone Number</div>
  <div class="field" style="left:260px;top:260px;width:680px;height:84px">Message</div>
  <span class="btn-submit">SUBMIT</span>
</section>

<footer class="site-footer">
  <div class="social"><i></i><i></i><i></i><i></i></div>
  <div class="contact-line">
    <svg width="12" height="16" viewBox="0 0 12 16"><path fill="#8dc63f" d="M6 0a6 6 0 0 0-6 6c0 4.5 6 10 6 10s6-5.5 6-10a6 6 0 0 0-6-6zm0 8.5A2.5 2.5 0 1 1 6 3.5a2.5 2.5 0 0 1 0 5z"/></svg>
    <span>48 Fern Lane, Suite 5, Harbor City</span><span>|</span>
    <svg width="14" height="14" viewBox="0 0 24 24"><path fill="#8dc63f" d="M6.6 10.8a15 15 0 0 0 6.6 6.6l2.2-2.2a1 1 0 0 1 1-.25 11.4 11.4 0 0 0 3.6.6 1 1 0 0 1 1 1V20a1 1 0 0 1-1 1A17 17 0 0 1 3 4a1 1 0 0 1 1-1h3.5a1 1 0 0 1 1 1c0 1.25.2 2.45.6 3.6a1 1 0 0 1-.25 1z"/></svg>
    <span>+61 400 555 210</span><span>|</span>
    <svg width="16" height="12" viewBox="0 0 16 12"><rect width="16" height="12" rx="1" fill="#8dc63f"/><path d="M1 1l7 5 7-5" fill="none" stroke="#fff" stroke-width="1.5"/></svg>
    <span>hello@verdantformnutrition.com</span>
  </div>
  <div class="links">Help &nbsp; | &nbsp; FAQ &nbsp; | &nbsp; Support &nbsp; | &nbsp; Sitemap &nbsp; | &nbsp; Terms Of Use &nbsp; | &nbsp; Privacy Statement</div>
  <div class="copy">Verdant Form Nutritional Therapy © 2019 All rights reserved.</div>
</footer>

</body>
</html>
```